Financial Advisor Resource Firm needs business card design

Need business card design for company in Omaha NE called Meridale Circle. We provide resources to financial advisors....workshop programs, retirement analysis, and insurance planning. I would like to see designs that use grays, greens, black, and white colors. The final design should communicate 'collaboration' and be simple yet attractive to financial planning clients. I will attached our logo and another picture of a puzzle piece coming together. I would like the incorporate the puzzle picture somehow, maybe on the back somehow, with color or just the gray scale....OR, the picture be the front of the card with 'Meridale' definition on it (see upload) and then company logo, employee name, title, address on the back (see ppt uploaded). The following disclosure needs to be included somewhere- Advisory services offered through Stonebrook Assets, LLC.
Updates

I uploaded a svg and ai file of the logo

Target Market(s)

Financial planning clients and financial advisors....so pretty diverse age range of about 40-70.

Industry/Entity Type

Financial Planning

Contact Information for Business Card

Tobias L. Fenwright, MBA
Founder/President
5287 E. Larkin Road
Suite 230
Omaha, NE 68190
Phone- (402) 555-0147
Cell- (402) 555-0183
Fax- (402) 555-0129
email- tobias@meridaleplan.example
web address- www.meridaleplan.example

Colors
1b1b1b
474747
d3d3d3
ffffff
9bcb3c
abd036

Requirements
Must have
• Must include logo provided, must be 2 sided, and must have disclosure...all of these items listed in project description

```html
<!DOCTYPE html>
<html lang="en">
<head>
<meta charset="utf-8">
<title>Meridale Circle – Business Card</title>
<link rel="stylesheet" href="https://fonts.googleapis.com/css2?family=Open+Sans:wght@400;600;700&display=swap">
<style>
  :root {
    --ink: #1b1b1b;
    --graphite: #474747;
    --silver: #d3d3d3;
    --paper: #ffffff;
    --leaf: #9bcb3c;
    --lime: #abd036;
    --sage-light: #c9d6b8;
    --sage-mid: #93a77c;
    --sage-dark: #4d5e3a;
    --stage: #ecece9;
  }
  * { margin: 0; padding: 0; box-sizing: border-box; }
  html, body { width: 1200px; height: 900px; overflow: hidden; }
  body {
    background: var(--stage);
    font-family: "Open Sans", Arial, sans-serif;
    position: relative;
  }
  .card {
    position: absolute;
    left: 290px;
    width: 620px;
    height: 354px;
    overflow: hidden;
    box-shadow: 0 6px 18px rgba(0,0,0,.18);
  }
  /* Back side */
  .card-back { top: 60px; }
  .back-photo {
    position: absolute; inset: 0;
    background:
      radial-gradient(ellipse at 65% 45%, var(--sage-dark) 0%, rgba(77,94,58,0) 55%),
      linear-gradient(120deg, var(--sage-light) 0%, var(--sage-mid) 55%, var(--sage-dark) 100%);
  }
  .back-brand {
    position: absolute; left: 0; right: 0; top: 128px;
    display: flex; align-items: center; justify-content: center; gap: 12px;
  }
  .back-brand .mark {
    width: 22px; height: 22px; border-radius: 50%;
    background: var(--ink);
  }
  .back-brand .name {
    font-size: 40px; font-weight: 600; letter-spacing: 2px;
    color: var(--ink); text-transform: uppercase;
  }
  .back-definition {
    position: absolute; left: 0; right: 0; bottom: 46px;
    text-align: center;
    font-size: 15px; letter-spacing: 2px;
    color: var(--ink); text-transform: uppercase;
  }
  /* Front side */
  .card-front { top: 486px; background: var(--paper); }
  .front-brand {
    position: absolute; top: 46px; right: 56px;
    display: flex; align-items: center; gap: 12px;
  }
  .front-brand .mark {
    width: 20px; height: 20px; border-radius: 50%;
    background: var(--leaf);
  }
  .front-brand .name {
    font-size: 34px; font-weight: 600; letter-spacing: 2px;
    color: var(--ink); text-transform: uppercase;
  }
  .person {
    position: absolute; right: 316px; top: 140px;
    text-align: right; color: var(--graphite);
    font-size: 15px; line-height: 22px;
  }
  .person .full-name {
    font-size: 21px; font-weight: 700; color: var(--leaf);
    line-height: 30px; white-space: nowrap;
  }
  .person .address { margin-top: 6px; }
  .divider {
    position: absolute; left: 318px; top: 148px;
    width: 1px; height: 100px; background: var(--graphite);
  }
  .contacts {
    position: absolute; left: 330px; top: 146px;
    list-style: none; color: var(--graphite);
    font-size: 15px; line-height: 20.5px;
  }
  .contacts li { display: flex; align-items: center; gap: 8px; }
  .contacts svg { width: 12px; height: 12px; fill: var(--graphite); flex: none; }
  .base-bands { position: absolute; left: 0; bottom: 0; width: 620px; height: 84px; }
  .disclosure {
    position: absolute; left: 0; right: 0; bottom: 18px;
    text-align: center;
    font-size: 12px; font-weight: 400; letter-spacing: .5px;
    color: var(--paper);
  }
</style>
</head>
<body>

<section class="card card-back" aria-label="Card back">
  <div class="back-photo" role="img" aria-label="Green-toned photograph of hands fitting puzzle pieces together"></div>
  <div class="back-brand">
    <span class="mark"></span>
    <span class="name">Meridale Circle</span>
  </div>
  <p class="back-definition">To come together and unite in common interest and focus</p>
</section>

<section class="card card-front" aria-label="Card front">
  <div class="front-brand">
    <span class="mark"></span>
    <span class="name">Meridale Circle</span>
  </div>

  <div class="person">
    <div class="full-name">Tobias L. Fenwright, MBA</div>
    <div class="title">Founder/President</div>
    <div class="address">5287 E. Larkin Road Suite 230<br>Omaha, NE 68190</div>
  </div>

  <div class="divider"></div>

  <ul class="contacts">
    <li>
      <svg viewBox="0 0 12 12" aria-hidden="true"><path d="M2.5 1l2 2.2-1 1.3c.7 1.5 1.8 2.6 3.3 3.3l1.3-1 2.2 2-1.1 1.9C5.6 10.5 1.5 6.4.6 2.1z"/></svg>
      <span>(402) 555-0147</span>
    </li>
    <li>
      <svg viewBox="0 0 12 12" aria-hidden="true"><path d="M3.5 0h5a1 1 0 0 1 1 1v10a1 1 0 0 1-1 1h-5a1 1 0 0 1-1-1V1a1 1 0 0 1 1-1zm.3 1.5v8h4.4v-8z"/></svg>
      <span>(402) 555-0183</span>
    </li>
    <li>
      <svg viewBox="0 0 12 12" aria-hidden="true"><path d="M3 0h5l1 1v3H3zM1 4.5h10v5H9V12H3V9.5H1zm3 5v1.5h4V9.5z"/></svg>
      <span>(402) 555-0129</span>
    </li>
    <li>
      <svg viewBox="0 0 12 12" aria-hidden="true"><path d="M0 2.5h12v7H0zm1 1v.4l5 3 5-3v-.4z"/></svg>
      <span>tobias@meridaleplan.example</span>
    </li>
    <li>
      <svg viewBox="0 0 12 12" aria-hidden="true"><circle cx="6" cy="6" r="5.5" fill="none" stroke="#474747" stroke-width="1"/><path d="M.5 6h11M6 .5v11" stroke="#474747" stroke-width="1"/><ellipse cx="6" cy="6" rx="2.4" ry="5.5" fill="none" stroke="#474747" stroke-width="1"/></svg>
      <span>www.meridaleplan.example</span>
    </li>
  </ul>

  <svg class="base-bands" viewBox="0 0 620 84" aria-hidden="true">
    <polygon points="0,0 440,0 452,8 0,8" fill="var(--ink)"/>
    <polygon points="0,10 452,10 462,18 0,18" fill="var(--silver)"/>
    <polygon points="0,22 455,22 475,10 620,10 620,84 0,84" fill="var(--leaf)"/>
  </svg>
  <p class="disclosure">Advisory services offered through Stonebrook Assets, LLC</p>
</section>

</body>
</html>
```